Website re-design and completion for www.brovimark.com

Graphically redesign and complete the existing site www.brovimark.com
This site intent is to:
a) introduce and educate about a new Technoloy to customers in a variety of different industries using traditional methods.
b) outline and promote the benefits and ROI of using the new techology
c) Sell our machines by showing customers the benefits and reasons to purchase from us over other suppliers
We do want to keep the overall concept. Like the home page with a slider. The most important thing to us is to increase the design of the slider. Next we need it standard layout with some attractive design to describe each product group. There are 3 product groups. Laser Cleaning Machines, Laser Welding Machines and Laser Cutting Machines

Target Market(s)

Mostly business to business.

Coding

Coded - Design and coding required

Font styles to use
Sans Serif
Other font styles liked:
• Calibri, Arial

Requirements
Must have
• A serious approach as we are targeting professionals, such as production managers, engineers and so forth
Should not have
• Annoying call to action stuff. Overly playful gimmicks.

```html
<!DOCTYPE html>
<html lang="en">
<head>
<meta charset="utf-8">
<title>Brovimark – Laser Cutting and Welding Equipment</title>
<link href="https://fonts.googleapis.com/css2?family=Outfit:wght@300;400;500&display=swap" rel="stylesheet">
<style>
:root{
  --blue:#0a7fd4;
  --navy:#0b3a6e;
  --ink:#1b1d24;
  --muted:#7b8190;
  --soft:#a9aec4;
  --line:#e6e8ef;
  --tint:#f7f7fd;
  --dark:#1f2140;
  --green:#3bb77e;
  --white:#fff;
}
*{margin:0;padding:0;box-sizing:border-box}
html,body{width:1200px;height:4161px;overflow:hidden}
body{font-family:"Outfit",Arial,sans-serif;color:var(--ink);background:var(--white);position:relative}
section,header,footer{position:absolute;left:0;width:1200px}
.abs{position:absolute}
a{color:inherit;text-decoration:none}

/* hero */
.hero{top:0;height:581px;background:linear-gradient(90deg,#1b2130 0%,#2b3140 45%,#4a4f58 70%,#3b3f47 100%)}
.hero-photo{position:absolute;inset:0;background:radial-gradient(circle at 63% 52%,rgba(255,196,110,.55) 0,rgba(255,160,60,.18) 14%,transparent 30%),linear-gradient(90deg,rgba(15,20,32,.9) 0%,rgba(15,20,32,.55) 45%,rgba(20,25,35,.2) 100%)}
.brand{font-weight:500;color:#e53935;font-size:30px;letter-spacing:.5px;display:flex;align-items:center;gap:10px}
.brand i{width:14px;height:14px;background:#e53935;display:block;border-radius:50%}
.nav{top:28px;left:460px;display:flex;gap:24px;color:#fff;font-size:15px}
.btn{display:inline-flex;align-items:center;gap:10px;background:var(--blue);color:#fff;border-radius:4px;font-size:14px}
.hero h1{left:134px;top:122px;width:460px;font-weight:400;font-size:45px;line-height:54px;color:#fff}
.hero p{left:134px;top:302px;width:430px;font-size:13px;line-height:27px;color:#dfe3ea}

/* stats */
.stats{top:581px;height:180px;border-bottom:1px solid var(--line)}
.stat{top:66px;display:flex;gap:10px;align-items:flex-start}
.stat b{font-weight:300;font-size:45px;line-height:1}
.stat span{font-size:14px;line-height:24px;color:var(--muted);width:120px;margin-top:-2px}

/* products */
.products{top:761px;height:580px}
.sec-title{width:1200px;text-align:center;font-weight:400;font-size:32px}
.sec-sub{width:1200px;text-align:center;color:var(--soft);font-size:16px;line-height:27px}
.card{top:227px;width:212px;height:314px;border:1px solid var(--line);border-radius:6px;overflow:hidden;background:#fff}
.card .ph{height:165px}
.card h3{font-weight:400;font-size:16px;margin:18px 8px 10px}
.card p{font-size:13.5px;line-height:24px;color:var(--muted);margin:0 8px}
.more{display:flex;gap:6px;align-items:center;color:var(--blue);font-size:14px;margin:14px 8px}

/* about */
.about{top:1341px;height:511px;background:var(--tint)}
.about h2{left:122px;top:155px;font-weight:400;font-size:45px;line-height:50px;color:var(--navy)}
.about p{left:122px;top:282px;width:520px;font-size:13px;line-height:25px;color:var(--soft)}
.arrow{width:36px;height:36px;border-radius:50%;background:#fff;display:flex;align-items:center;justify-content:center}

/* services */
.services{top:1852px;height:592px}
.eyebrow{color:var(--blue);font-size:20px}
.services h2{font-weight:400;font-size:28px;color:var(--navy)}
.list{list-style:none}
.list li{display:flex;gap:14px;align-items:center;font-size:14px;color:var(--navy);height:35px}

/* reasons */
.reasons{top:2444px;height:511px;background:linear-gradient(180deg,#f5f6fd 0%,#fff 100%)}
.reasons h2{left:128px;top:118px;font-weight:400;font-size:32px;line-height:40px}
.reasons p{left:128px;top:218px;width:400px;font-size:15px;line-height:27px;color:var(--muted)}
.feat{display:flex;gap:12px;align-items:center;font-size:16px}

/* consultancy */
.consult{top:2955px;left:3px;width:1197px;height:619px;background:var(--dark)}
.consult h2{left:127px;top:200px;width:340px;font-weight:400;font-size:32px;line-height:40px;color:#fff}
.consult p{left:127px;top:352px;width:310px;font-size:16px;line-height:27px;color:#c4c7da}
.form{left:806px;top:105px;width:263px;height:416px;background:#fff;border-radius:6px;padding:22px 19px}
.form label{display:block;font-size:12px;color:var(--ink);margin-bottom:10px}
.field{height:40px;border:1px solid var(--line);border-radius:4px;font-size:12px;color:var(--muted);display:flex;align-items:center;justify-content:space-between;padding:0 14px;margin-bottom:18px}

/* newsletter */
.news{top:3574px;height:206px}
.news h2{left:140px;top:78px;font-weight:400;font-size:28px;line-height:37px}

/* footer */
.foot{top:3780px;height:381px}
.foot h4{font-weight:500;font-size:15px;margin-bottom:14px}
.foot .col a{display:block;font-size:15px;color:#535a6b;margin-bottom:17px}
.ci{display:flex;gap:10px;align-items:flex-start;font-size:15px;color:#535a6b;margin-bottom:17px;line-height:19px}
.soc{width:34px;height:34px;border-radius:50%;background:var(--blue)}
.small{font-size:13px;color:var(--muted)}
</style>
</head>
<body>

<header class="hero">
  <div class="hero-photo" role="img" aria-label="Photo of a technician in a workshop with sparks flying from a laser cutting machine"></div>
  <div class="abs brand" style="left:118px;top:20px"><i></i>BROVIMARK</div>
  <nav class="abs nav"><a>Home</a><a>Product</a><a>About</a><a>Services</a><a>Contact</a></nav>
  <a class="abs btn" style="left:975px;top:17px;height:40px;padding:0 18px">Contact us</a>
  <h1 class="abs">Discover the Future of Manufacturing with Brovimark</h1>
  <p class="abs">Forem ipsum dolor sit amet, consectetur adipiscing elit. Nunc vulputate libero et velit interdum, ac aliquet odio mattis. Class aptent taciti sociosqu ad litora torquent per conubia nostra, per inceptos himenaeos.</p>
  <a class="abs btn" style="left:134px;top:432px;height:48px;padding:0 18px">Get started now
    <svg width="14" height="14" viewBox="0 0 14 14"><path d="M1 7h11M8 3l4 4-4 4" stroke="#fff" stroke-width="1.6" fill="none"/></svg></a>
</header>

<section class="stats">
  <div class="abs stat" style="left:216px"><b>1M+</b><span>Customers visit Brovimark every months</span></div>
  <div class="abs stat" style="left:496px"><b>93%</b><span>Satisfaction rate from our customers.</span></div>
  <div class="abs stat" style="left:784px"><b>4.9</b><span>Average customer ratings out of 5.00!</span></div>
</section>

<section class="products">
  <h2 class="abs sec-title" style="top:68px">Product we offer for you</h2>
  <p class="abs sec-sub" style="top:122px">Torem ipsum dolor sit amet, consectetur adipiscing elit. Nunc<br>vulputate libero et velit interdum.</p>
  <article class="abs card" style="left:118px"><div class="ph" role="img" aria-label="Photo of laser welding torch on metal" style="background:linear-gradient(135deg,#6b6460,#c9c2bb 55%,#8a7d70)"></div><h3>Laser Welding</h3><p>Qorem ipsum dolor sit amet, consectetur adipiscing elit.</p><a class="more">Learn more <svg width="14" height="12" viewBox="0 0 14 12"><path d="M1 6h11M8 2l4 4-4 4" stroke="#0a7fd4" stroke-width="1.6" fill="none"/></svg></a></article>
  <article class="abs card" style="left:368px"><div class="ph" role="img" aria-label="Photo of laser cutting head with sparks" style="background:radial-gradient(circle at 50% 70%,#ffe3a0,#d98b2a 35%,#5a3b20 80%)"></div><h3>Laser Cutting</h3><p>Qorem ipsum dolor sit amet, consectetur adipiscing elit.</p><a class="more">Learn more <svg width="14" height="12" viewBox="0 0 14 12"><path d="M1 6h11M8 2l4 4-4 4" stroke="#0a7fd4" stroke-width="1.6" fill="none"/></svg></a></article>
  <article class="abs card" style="left:619px"><div class="ph" role="img" aria-label="Photo of a cleaned metal surface" style="background:radial-gradient(circle at 50% 45%,#d8d3cf,#8a8480 60%,#5e5955)"></div><h3>Laser Cleaning</h3><p>Qorem ipsum dolor sit amet, consectetur adipiscing elit.</p><a class="more">Learn more <svg width="14" height="12" viewBox="0 0 14 12"><path d="M1 6h11M8 2l4 4-4 4" stroke="#0a7fd4" stroke-width="1.6" fill="none"/></svg></a></article>
  <article class="abs card" style="left:869px"><div class="ph" role="img" aria-label="Photo of a spool of copper welding wire" style="background:radial-gradient(ellipse at 50% 50%,#c8703f 0,#8a4426 25%,#fff 40%)"></div><h3>Accesories</h3><p>Qorem ipsum dolor sit amet, consectetur adipiscing elit.</p><a class="more">Learn more <svg width="14" height="12" viewBox="0 0 14 12"><path d="M1 6h11M8 2l4 4-4 4" stroke="#0a7fd4" stroke-width="1.6" fill="none"/></svg></a></article>
</section>

<section class="about">
  <h2 class="abs">Discover About<br>Brovimark</h2>
  <p class="abs">SaaS become a common delivery model for many business application, including office software, messaging software, payroll processing software, DBMS software, management software</p>
  <div class="abs" role="img" aria-label="Photo of two engineers beside a laser machine in a factory" style="left:703px;top:92px;width:383px;height:326px;background:linear-gradient(135deg,#2d4a6a,#6a7d8e 50%,#a9b0b6)"></div>
  <div class="abs arrow" style="left:974px;top:440px"><svg width="12" height="14" viewBox="0 0 12 14"><path d="M8 2 3 7l5 5" stroke="#1b1d24" stroke-width="1.6" fill="none"/></svg></div>
  <div class="abs arrow" style="left:1048px;top:440px"><svg width="12" height="14" viewBox="0 0 12 14"><path d="m4 2 5 5-5 5" stroke="#1b1d24" stroke-width="1.6" fill="none"/></svg></div>
</section>

<section class="services">
  <svg class="abs" style="left:0;top:89px" width="440" height="413" viewBox="0 0 440 413"><path d="M0 0H275L440 413H0Z" fill="#eef0f7"/></svg>
  <div class="abs" role="img" aria-label="Product photo of a wheeled laser source unit" style="left:60px;top:157px;width:483px;height:276px;border-radius:4px;background:linear-gradient(90deg,#e7e8ea,#fbfbfb 45%,#d8d9db);box-shadow:0 20px 40px rgba(30,40,80,.12)"></div>
  <div class="abs eyebrow" style="left:614px;top:88px">Services we offer for you</div>
  <h2 class="abs" style="left:614px;top:124px">Laser Equipment Repair</h2>
  <p class="abs" style="left:614px;top:170px;width:460px;font-size:13.5px;line-height:25px;color:var(--muted)">In addition to providing domestically-stocked laser manufacturing equipment, Brovimark offers support and repair services on laser welding, laser cutting, and laser cleaning machinery.</p>
  <ul class="abs list" style="left:614px;top:250px">
    <li><svg width="16" height="16" viewBox="0 0 16 16"><circle cx="8" cy="8" r="8" fill="#e5f6ed"/><path d="m4.5 8 2.3 2.3L11.5 5.6" stroke="#3bb77e" stroke-width="1.6" fill="none"/></svg>Torem ipsum dolor sit amet, consectetur adipiscing elit.</li>
    <li><svg width="16" height="16" viewBox="0 0 16 16"><circle cx="8" cy="8" r="8" fill="#e5f6ed"/><path d="m4.5 8 2.3 2.3L11.5 5.6" stroke="#3bb77e" stroke-width="1.6" fill="none"/></svg>Lorem ipsum dolor sit</li>
    <li><svg width="16" height="16" viewBox="0 0 16 16"><circle cx="8" cy="8" r="8" fill="#e5f6ed"/><path d="m4.5 8 2.3 2.3L11.5 5.6" stroke="#3bb77e" stroke-width="1.6" fill="none"/></svg>Worem ipsum dolor sit amet consectetur</li>
    <li><svg width="16" height="16" viewBox="0 0 16 16"><circle cx="8" cy="8" r="8" fill="#e5f6ed"/><path d="m4.5 8 2.3 2.3L11.5 5.6" stroke="#3bb77e" stroke-width="1.6" fill="none"/></svg>Jorem ipsum dolor sit amet&nbsp; consectetur consectetur</li>
    <li><svg width="16" height="16" viewBox="0 0 16 16"><circle cx="8" cy="8" r="8" fill="#e5f6ed"/><path d="m4.5 8 2.3 2.3L11.5 5.6" stroke="#3bb77e" stroke-width="1.6" fill="none"/></svg>Qorem ipsum dolor</li>
  </ul>
  <a class="abs" style="left:614px;top:463px;width:153px;height:44px;border:1.5px solid var(--blue);border-radius:4px;display:flex;align-items:center;justify-content:center;gap:14px;color:var(--blue);font-size:12px">Book a service
    <svg width="16" height="16" viewBox="0 0 16 16"><path d="M9 2h5v5M14 2 7 9M12 10v4H2V4h4" stroke="#0a7fd4" stroke-width="1.4" fill="none"/></svg></a>
</section>

<section class="reasons">
  <h2 class="abs">Reasons you should<br>choose us.</h2>
  <p class="abs">We share common trends and strategies for improving your rental income and making sure you stay in high demand.</p>
  <div class="abs feat" style="left:128px;top:334px"><svg width="16" height="12" viewBox="0 0 16 12"><path d="m1 6 4.5 4.5L15 1" stroke="#0a7fd4" stroke-width="1.8" fill="none"/></svg>Fully Responsive</div>
  <div class="abs feat" style="left:398px;top:334px"><svg width="16" height="12" viewBox="0 0 16 12"><path d="m1 6 4.5 4.5L15 1" stroke="#0a7fd4" stroke-width="1.8" fill="none"/></svg>Forem ipsum</div>
  <div class="abs feat" style="left:128px;top:377px"><svg width="16" height="12" viewBox="0 0 16 12"><path d="m1 6 4.5 4.5L15 1" stroke="#0a7fd4" stroke-width="1.8" fill="none"/></svg>Sorem ipsum dolor sit</div>
  <div class="abs feat" style="left:398px;top:377px"><svg width="16" height="12" viewBox="0 0 16 12"><path d="m1 6 4.5 4.5L15 1" stroke="#0a7fd4" stroke-width="1.8" fill="none"/></svg>Worem ipsum dolor</div>
  <div class="abs" role="img" aria-label="Banner image of a laser machine workshop" style="left:658px;top:153px;width:324px;height:80px;border-radius:3px;background:linear-gradient(90deg,#2a3550,#55627a);box-shadow:0 10px 24px rgba(20,30,60,.18)"></div>
  <div class="abs" role="img" aria-label="Banner image for laser cleaning equipment" style="left:782px;top:250px;width:296px;height:76px;border-radius:3px;background:linear-gradient(90deg,#3c4556,#b8a290 45%,#eef0f4);box-shadow:0 10px 24px rgba(20,30,60,.18)"></div>
  <div class="abs" role="img" aria-label="Banner image for laser welding machines" style="left:700px;top:342px;width:316px;height:78px;border-radius:3px;background:linear-gradient(90deg,#2e3a55,#6a7288 50%,#e7e9ee);box-shadow:0 10px 24px rgba(20,30,60,.18)"></div>
</section>

<section class="consult">
  <svg class="abs" style="left:0;top:0" width="1197" height="619" viewBox="0 0 1197 619"><g stroke="#3a2f4d" stroke-width="1.2" fill="none"><path d="M40 0C120 200 60 420 160 619"/><path d="M240 0C320 220 260 400 360 619"/><path d="M460 0C540 200 480 420 580 619"/><path d="M700 0C780 200 720 420 820 619"/><path d="M940 0C1020 200 960 420 1060 619"/></g></svg>
  <div class="abs" style="left:127px;top:107px;width:66px;height:66px;border-radius:50%;background:#2c2f4f;display:flex;align-items:center;justify-content:center">
    <svg width="28" height="26" viewBox="0 0 28 26"><path d="M14 1C7 1 1 5.5 1 11c0 3 1.7 5.6 4.4 7.4L4 25l7-4c1 .2 2 .3 3 .3 7 0 13-4.5 13-10S21 1 14 1Z" fill="#5cd18b"/></svg></div>
  <h2 class="abs">Get a free consultancy from our expert right now!</h2>
  <p class="abs">Gorem ipsum dolor sit amet, consectetur adipiscing elit. Nunc vulputate libero et velit interdum, ac aliquet odio mattis.</p>
  <form class="abs form">
    <label>Company name</label><div class="field">Your name</div>
    <label>Email</label><div class="field">Email</div>
    <label>Phone</label><div class="field">phone number</div>
    <label>Which service do you need?</label><div class="field">Select a service <svg width="8" height="5" viewBox="0 0 8 5"><path d="M0 0h8L4 5Z" fill="#1b1d24"/></svg></div>
    <div class="btn" style="width:225px;height:48px;justify-content:center;font-size:14px">Get Free Consultancy</div>
  </form>
</section>

<section class="news">
  <h2 class="abs">Qorem ipsum dolor sit amet,<br>consectetur adipiscing elit.</h2>
  <div class="abs field" style="left:665px;top:76px;width:250px;height:48px;margin:0">Enter your email</div>
  <a class="abs btn" style="left:924px;top:76px;height:48px;padding:0 18px;gap:26px">Contact us
    <svg width="14" height="14" viewBox="0 0 14 14"><path d="M1 7h11M8 3l4 4-4 4" stroke="#fff" stroke-width="1.6" fill="none"/></svg></a>
</section>

<footer class="foot">
  <div class="abs brand" style="left:106px;top:46px;font-size:32px"><i></i>BROVIMARK</div>
  <div class="abs soc" style="left:106px;top:135px"></div>
  <div class="abs soc" style="left:163px;top:135px;background:#eef0f7"></div>
  <div class="abs soc" style="left:220px;top:135px"></div>
  <div class="abs col" style="left:647px;top:48px"><h4>Pages</h4><a>Home</a><a>Product</a><a>About</a><a>Services</a><a>Contact</a></div>
  <div class="abs" style="left:852px;top:48px;width:240px"><h4>Contact</h4>
    <div class="ci"><svg width="18" height="18" viewBox="0 0 18 18"><path d="M4 1.5 6.5 4 5 6.5c1 2.5 3.5 5 6 6l2.5-1.5 2.5 2.5-1.5 3C8 16 2 10 1.5 3Z" stroke="#535a6b" stroke-width="1.3" fill="none"/></svg>555-014-2270</div>
    <div class="ci"><svg width="18" height="18" viewBox="0 0 18 18"><rect x="1.5" y="3.5" width="15" height="11" rx="2" stroke="#535a6b" stroke-width="1.3" fill="none"/><path d="m2 5 7 5 7-5" stroke="#535a6b" stroke-width="1.3" fill="none"/></svg>info@brovimark.com</div>
    <div class="ci"><svg width="18" height="18" viewBox="0 0 18 18"><circle cx="9" cy="9" r="7.5" stroke="#535a6b" stroke-width="1.3" fill="none"/><path d="M9 4.5V9l3 2" stroke="#535a6b" stroke-width="1.3" fill="none"/></svg>Tuesday – Friday 8:00 am – 5:00 pm</div>
    <div class="ci"><svg width="18" height="18" viewBox="0 0 18 18"><path d="M9 17s6-5.5 6-10A6 6 0 0 0 3 7c0 4.5 6 10 6 10Z" stroke="#535a6b" stroke-width="1.3" fill="none"/><circle cx="9" cy="7" r="2" stroke="#535a6b" stroke-width="1.3" fill="none"/></svg>Maple Ridge, IL 60990</div>
  </div>
  <div class="abs small" style="left:106px;top:307px">Copyright, Brovimark 2024. All rights reserved.</div>
  <div class="abs small" style="left:965px;top:307px">Terms &amp; Conditions</div>
</footer>

</body>
</html>
```